Simple Logo Design for Semi-Clear Plastic Frosted Card stock

Create a business card on frosted plastic. compliment existing logo elements with a tree trunk, roots, or seed at the lower half and the full logo both on the front.

Contact information will go on a solid portion of the back of this design since this card stock is semi-transparent.

It is important to consider this plastic card stock medium in your design. I found helpful tips and guides listed at vellaprint-sample.net: be careful to understand ink printed on plastic cards cannot have too much of a consistent print area or risks peeling and fine lines can easily scratch off.
Updates

2" x 3.5" 20PT Clear Plastic Business cards with Round corners Please get info or templates here: https://www.vellaprint-sample.net/product-detail/2-x-35-20pt-clear-plastic-business-cards-with-round-corners

Target Market(s)

Not for profit- religion

Industry/Entity Type

Business

Must include complementary elements to the existing logo

Font styles to use
Decorative

Colors
000000

Requirements
Must have
• Elements of community, nature and oneness. Such as: seed, roots, tree trunk, etc.
• Three lines of space on the back for Name, Title, Phone Number.
Nice to have
• I like a light use of decorative elements
Should not have
• No eyes, from faces or animals.

```html
<!DOCTYPE html>
<html lang="en">
<head>
<meta charset="utf-8">
<title>Steadfast Grove – Frosted Business Card</title>
<link rel="stylesheet" href="https://fonts.googleapis.com/css2?family=Questrial&family=Roboto:wght@400&display=swap">
<style>
  :root {
    --bg: #e6e2dc;
    --frost-top: #f4f5f4;
    --frost-bottom: #d9dcdb;
    --band: #1e4b45;
    --band-deep: #163a35;
    --leaf: #3d8b2b;
    --leaf-light: #6cb24a;
    --brand: #1e4b45;
    --ink: #2f3332;
    --on-band: #e9efed;
  }
  * { margin: 0; padding: 0; box-sizing: border-box; }
  html, body {
    width: 1200px;
    height: 969px;
    overflow: hidden;
    background: var(--bg);
  }
  .canvas {
    position: relative;
    width: 1200px;
    height: 969px;
  }
  .card {
    position: absolute;
    left: 100px;
    top: 199px;
    width: 1000px;
    height: 571px;
    border-radius: 26px;
    overflow: hidden;
    background: linear-gradient(170deg, var(--frost-top), var(--frost-bottom));
    box-shadow: 0 0 0 1px rgba(255,255,255,0.7) inset, 0 6px 18px rgba(0,0,0,0.12);
  }
  .card-art {
    position: absolute;
    inset: 0;
    width: 100%;
    height: 100%;
  }
  .holder-line {
    position: absolute;
    left: 425px;
    top: 32px;
    font-family: "Roboto", Arial, sans-serif;
    font-size: 29px;
    color: var(--on-band);
    letter-spacing: 0.3px;
  }
  .holder-line .holder-name { font-weight: 400; }
  .holder-line .holder-title { opacity: 0.9; }
  .brand {
    position: absolute;
    left: 0;
    right: 0;
    top: 330px;
    display: flex;
    justify-content: center;
    align-items: center;
    gap: 18px;
  }
  .brand-dot {
    width: 40px;
    height: 40px;
    border-radius: 50%;
    background: var(--brand);
  }
  .brand-name {
    font-family: "Questrial", "Century Gothic", sans-serif;
    font-size: 54px;
    color: var(--brand);
    letter-spacing: 1px;
  }
  .phone {
    position: absolute;
    left: 0;
    right: 0;
    top: 484px;
    text-align: center;
    font-family: "Roboto", Arial, sans-serif;
    font-size: 40px;
    color: var(--ink);
    letter-spacing: 0.5px;
  }
</style>
</head>
<body>
  <main class="canvas">
    <section class="card" aria-label="Steadfast Grove business card, front">
      <svg class="card-art" viewBox="0 0 1000 571" preserveAspectRatio="none" aria-hidden="true">
        <defs>
          <linearGradient id="bandShade" x1="0" y1="0" x2="0" y2="1">
            <stop offset="0" stop-color="var(--band-deep)"/>
            <stop offset="1" stop-color="var(--band)"/>
          </linearGradient>
          <linearGradient id="leafShade" x1="0" y1="0" x2="1" y2="0">
            <stop offset="0" stop-color="var(--leaf-light)"/>
            <stop offset="1" stop-color="var(--leaf)"/>
          </linearGradient>
        </defs>
        <path class="top-band" fill="url(#bandShade)"
              d="M0,0 H1000 V128 C850,105 600,92 300,118 C170,130 60,170 0,214 Z"/>
        <path class="leaf-swoosh" fill="url(#leafShade)"
              d="M300,118 C600,92 850,105 1000,128 V290 C960,190 700,124 300,118 Z"/>
      </svg>

      <p class="holder-line">
        <span class="holder-name">Tamsin</span>
        <span class="holder-title"> - President</span>
      </p>

      <div class="brand">
        <span class="brand-dot"></span>
        <span class="brand-name">STEADFAST GROVE</span>
      </div>

      <p class="phone">555 0142 7789</p>
    </section>
  </main>
</body>
</html>
```